London Whisky Bottle Label

BACKGROUND
We are plumbers that have resurrected London's oldest once illicit Gin Distillery Harlow Post Wire https://www.vidtrove-example.net/clip/kq83pz
Bought 150yr old derelict bakery & turned it into an office for our plumbing biz....removed dangerous chimney...got sued by a neighbour ..
our lawyers discovered that the original bakers family once made illict gin here (in what is now our office) we tracked down the origianl family ...see pic enclosed....the little boy now in his 90's (Colin Treadle) gave us his family's secret gin recipe and we have now resurrected it. We supply Ravensmoor Hall, Hse of Wardens Pelling Drue etc. Now have our 1st London Whisky.
This is NOT scotch whisky...this a brand new category of drink 'English Whisky'
1. traditional whisky style bottle which will have embossed text on as per the sample English Whisky & K T Distillery LONDON
Front label 110mm x 95mm
Rear label 70mm wide and 100mm
Front Text TBC
Rear Text TBC
Must have a old map of my area London Q7 2XZ on rear
Map link https://charts.oldsheet-example.org/view/558210#zoom=6

Target Market(s)

OVER 30's

Font styles to use
Sans Serif

Requirements
Nice to have
• I want an old map on the front of the label....the map have 2 small rivers on it which are very close to my distillery (called The Hollin Race and Catter Beck, where they meet there a small bridge called Gravewick Bridge, i would like this shown on the map, is there any tasteful way to add some colour to the historic map ???

```html
<!DOCTYPE html>
<html lang="en">
<head>
<meta charset="utf-8">
<title>English Whisky — Front and Rear Labels</title>
<link rel="stylesheet" href="https://fonts.googleapis.com/css2?family=Old+Standard+TT:wght@400;700&family=PT+Serif:wght@700&display=swap">
<style>
  :root {
    --page: #ffffff;
    --label-front: #dcd8cc;
    --label-rear: #d6d0c6;
    --claret: #8a1c18;
    --claret-deep: #7a1713;
    --ribbon: #b9a88e;
    --ink: #2b2420;
    --map-light: #ece8d8;
    --map-mid: #d8d3bf;
  }
  * { box-sizing: border-box; margin: 0; padding: 0; }
  html, body {
    width: 1200px; height: 1200px; overflow: hidden;
    background: var(--page);
  }
  .canvas { position: relative; width: 1200px; height: 1200px; }

  .label { position: absolute; }
  .label-frame { position: absolute; inset: 0; width: 100%; height: 100%; }

  /* Front label */
  .front-label { left: 60px; top: 330px; width: 560px; height: 467px; background: var(--label-front); }
  .banner-text {
    font-family: "Old Standard TT", serif; font-size: 30px; fill: var(--claret);
    letter-spacing: 1px;
  }
  .name-front {
    position: absolute; left: 0; right: 0; top: 160px; text-align: center;
    font-family: "Old Standard TT", serif; font-weight: 700; font-size: 116px; line-height: 1;
    letter-spacing: 4px; color: var(--claret-deep);
  }
  .distillery-line {
    position: absolute; left: 0; right: 0; top: 312px; text-align: center;
    font-family: "Old Standard TT", serif; font-size: 20px; letter-spacing: 4px;
    color: var(--claret);
  }
  .est-text {
    font-family: "PT Serif", serif; font-weight: 700; font-size: 14px; fill: var(--claret);
  }

  /* Rear label */
  .rear-label { left: 700px; top: 280px; width: 400px; height: 568px; background: var(--label-rear); }
  .name-rear {
    position: absolute; left: 0; right: 0; top: 28px; text-align: center;
    font-family: "Old Standard TT", serif; font-weight: 700; font-size: 66px; line-height: 1;
    letter-spacing: 2px; color: var(--claret-deep);
  }
  .rear-intro {
    position: absolute; left: 18px; right: 18px; top: 128px; text-align: center;
    font-family: "Old Standard TT", serif; font-size: 12.5px; line-height: 16.5px; color: var(--ink);
  }
  .area-map {
    position: absolute; left: 15px; top: 186px; width: 360px; height: 249px;
    background: linear-gradient(160deg, var(--map-light) 0%, var(--map-mid) 55%, var(--map-light) 100%);
  }
  .volume {
    position: absolute; left: 0; right: 0; top: 456px; text-align: center;
    font-family: "Old Standard TT", serif; font-size: 12px; color: var(--ink);
  }
  .rear-notes {
    position: absolute; left: 0; right: 0; top: 477px; text-align: center;
    font-family: "Old Standard TT", serif; font-size: 12px; line-height: 16.5px; color: var(--ink);
  }
</style>
</head>
<body>
<main class="canvas">

  <section class="label front-label" aria-label="Front label">
    <svg class="label-frame" viewBox="0 0 560 467" aria-hidden="true">
      <path d="M41 36 H529 A14 14 0 0 0 543 50 V429 A14 14 0 0 0 529 443 H41 A14 14 0 0 0 27 429 V50 A14 14 0 0 0 41 36 Z"
            fill="none" stroke="var(--claret)" stroke-width="3"/>
      <path d="M66 118 Q286 50 510 118 Q518 140 500 160 Q286 96 78 160 Q60 140 66 118 Z"
            fill="none" stroke="var(--claret)" stroke-width="1.6"/>
      <path id="banner-curve" d="M96 146 Q286 80 480 146" fill="none"/>
      <text class="banner-text"><textPath href="#banner-curve" startOffset="50%" text-anchor="middle">ENGLISH WHISKY</textPath></text>
      <path d="M168 352 Q285 338 400 352 L392 376 Q285 364 176 376 Z M176 376 L168 398 Q285 388 400 398 L392 376"
            fill="none" stroke="var(--ribbon)" stroke-width="1.2"/>
      <text class="est-text" x="284" y="387" text-anchor="middle">Est. 1920</text>
    </svg>
    <div class="name-front">TBC</div>
    <p class="distillery-line">K.T. DISTILLERY LONDON</p>
  </section>

  <section class="label rear-label" aria-label="Rear label">
    <svg class="label-frame" viewBox="0 0 400 568" aria-hidden="true">
      <path d="M20 2 H380 A18 18 0 0 0 398 20 V548 A18 18 0 0 0 380 566 H20 A18 18 0 0 0 2 548 V20 A18 18 0 0 0 20 2 Z"
            fill="none" stroke="var(--claret)" stroke-width="3"/>
    </svg>
    <div class="name-rear">TBC</div>
    <p class="rear-intro">Lorem ipsum dolor sit amet, consectetuer adipiscing elit, sed diam nonummy nibh euismod tincidunt ut laoreet dolore magna aliquam erat volutpat. Ut wisi enim ad minim veniam, quis</p>
    <div class="area-map" role="img" aria-label="Historic Ordnance Survey style map of the distillery area around Q7 2XZ, showing The Hollin Race, Catter Beck and Gravewick Bridge"></div>
    <p class="volume">800 ML</p>
    <p class="rear-notes">Lorem ipsum dolor sit amet,<br>consectetuer adipiscing<br>elit, sed diam nonummy<br>nibh euismod</p>
  </section>

</main>
</body>
</html>
```